VOMRA Pty Ltd Business Card

Looking for a simple yet eye-catching double-sided business card design using my company logo on one side and contact details on the other.

Target Market(s)

Government

Industry/Entity Type

Communication Systems Engineering

Contact Information for Business Card

VOMRA Pty Ltd

Requirements
Nice to have
• Would be great to have a QR code so details can be scanned into contacts

```html
<!DOCTYPE html>
<html lang="en">
<head>
<meta charset="UTF-8">
<title>VOMRA Pty Ltd Business Card</title>
<link rel="stylesheet" href="https://fonts.googleapis.com/css2?family=Open+Sans:wght@400;600;700&display=swap">
<style>
  :root {
    --backdrop: #222222;
    --card-white: #ffffff;
    --slate: #37424a;
    --slate-deep: #273037;
    --ink-light: #ffffff;
    --rule: #c9ced2;
  }
  * { box-sizing: border-box; margin: 0; padding: 0; }
  html, body {
    width: 1200px;
    height: 780px;
    overflow: hidden;
    background: var(--backdrop);
    font-family: "Open Sans", sans-serif;
  }
  .canvas {
    position: relative;
    width: 1200px;
    height: 780px;
  }
  .card {
    position: absolute;
    width: 540px;
    height: 308px;
    border-radius: 22px;
    overflow: hidden;
    background: var(--card-white);
  }
  .card--front { left: 60px; top: 70px; }
  .card--back { left: 600px; top: 400px; }
  .card__shape {
    position: absolute;
    inset: 0;
    width: 100%;
    height: 100%;
  }
  .brand {
    position: absolute;
    display: flex;
    align-items: center;
    white-space: nowrap;
    font-weight: 700;
  }
  .brand__dot {
    border-radius: 50%;
    flex: none;
  }
  .card--front .brand {
    left: 0; right: 0; top: 118px;
    justify-content: center;
    gap: 14px;
    font-size: 62px;
    letter-spacing: 4px;
    color: var(--slate-deep);
  }
  .card--front .brand__dot {
    width: 44px; height: 44px;
    background: var(--slate-deep);
  }
  .card--back .brand {
    left: 52px; top: 176px;
    gap: 10px;
    font-size: 32px;
    letter-spacing: 2px;
    color: var(--ink-light);
  }
  .card--back .brand__dot {
    width: 24px; height: 24px;
    background: var(--ink-light);
  }
  .divider {
    position: absolute;
    left: 262px; top: 70px;
    width: 1px; height: 170px;
    background: var(--rule);
  }
  .contact {
    position: absolute;
    left: 286px; top: 64px;
    color: var(--ink-light);
  }
  .contact__name { font-size: 22px; font-weight: 700; line-height: 1.1; }
  .contact__role { font-size: 14px; font-weight: 400; margin-bottom: 12px; }
  .contact__address { font-size: 13px; line-height: 1.35; margin-bottom: 12px; }
  .contact__list { list-style: none; font-size: 13px; line-height: 1.5; }
  .contact__list li { display: flex; align-items: center; gap: 8px; }
  .contact__icon { width: 12px; height: 12px; flex: none; }
</style>
</head>
<body>
<main class="canvas">

  <section class="card card--front" aria-label="Card front">
    <svg class="card__shape" viewBox="0 0 540 308" aria-hidden="true">
      <ellipse cx="270" cy="150" rx="300" ry="190" transform="rotate(-22 270 150)" fill="var(--slate)"/>
    </svg>
    <div class="brand"><span class="brand__dot"></span><span class="brand__name">VOMRA</span></div>
  </section>

  <section class="card card--back" aria-label="Card back">
    <svg class="card__shape" viewBox="0 0 540 308" aria-hidden="true">
      <ellipse cx="270" cy="160" rx="300" ry="190" transform="rotate(-22 270 160)" fill="var(--slate)"/>
    </svg>
    <div class="brand"><span class="brand__dot"></span><span class="brand__name">VOMRA</span></div>
    <div class="divider"></div>
    <div class="contact">
      <p class="contact__name">Jordan Hale</p>
      <p class="contact__role">Co-Founder</p>
      <p class="contact__address">42-44 Harlow Street Ashby<br>Vale NSW 2093 Australia</p>
      <ul class="contact__list">
        <li>
          <svg class="contact__icon" viewBox="0 0 24 24" aria-hidden="true"><path fill="#fff" d="M6.6 10.8a15.1 15.1 0 0 0 6.6 6.6l2.2-2.2a1 1 0 0 1 1-.25 11.4 11.4 0 0 0 3.6.57 1 1 0 0 1 1 1V20a1 1 0 0 1-1 1A17 17 0 0 1 3 4a1 1 0 0 1 1-1h3.5a1 1 0 0 1 1 1c0 1.25.2 2.45.57 3.57a1 1 0 0 1-.25 1z"/></svg>
          <span>(555) 214-6093</span>
        </li>
        <li>
          <svg class="contact__icon" viewBox="0 0 24 24" aria-hidden="true"><circle cx="12" cy="12" r="10" fill="none" stroke="#fff" stroke-width="2"/><path d="M2 12h20M12 2c3 3 3 17 0 20M12 2c-3 3-3 17 0 20" fill="none" stroke="#fff" stroke-width="1.6"/></svg>
          <span>www.vomra.com.au</span>
        </li>
        <li>
          <svg class="contact__icon" viewBox="0 0 24 24" aria-hidden="true"><rect x="2" y="5" width="20" height="14" rx="1.5" fill="#fff"/><path d="M3 6l9 7 9-7" fill="none" stroke="var(--slate)" stroke-width="1.8"/></svg>
          <span>admin@vomra.com.au</span>
        </li>
      </ul>
    </div>
  </section>

</main>
</body>
</html>
```